Fun, Clean Business Card For Family Focused Travel Agency

I need a business card using specific colors and fonts as in the uploaded files. Ideally, I would like a large image of the logo on the back and all the contact info on the front. Maybe the stars/dots somewhere in a flowy form.

I do want it the contact information to be clear and easy to read. I don't want it to look too busy. Maybe even a bit minimalist.

I plan or ordering the ROUNDED CORNER business cards from Cardwell Press, so please consider that in your design.

Target Market(s)

Families with children, couples, groups of friends

Contact Information for Business Card

Marla Quint, Owner
Marla@TumbleTrips.example
Cell Phone Number 555-218-4603
Office Phone Number 555-647-1925
Specializing in Glimmerland destinations, Pelican Bay Fun Park, Cruises and All-Inclusive Vacations.

Nice but not required:
www.TumbleTrips.example
Facebook, Instagram, Twitter icons with username: TumbleTrips

Font styles to use
Sans Serif

Requirements
Must have
• Please try to use the colors from the logo as much as possible. I understand lighter shades/colors may be needed for some things.
Should not have
• NO SERIF FONTS. That is really the only thing I do not want at all

```html
<!DOCTYPE html>
<html lang="en">
<head>
<meta charset="utf-8">
<title>Tumble Trips Business Card</title>
<link rel="stylesheet" href="https://fonts.googleapis.com/css2?family=Courgette&family=Open+Sans:wght@400;600;700&display=swap">
<style>
  :root {
    --navy: #12173a;
    --teal: #1fb39a;
    --white: #ffffff;
    --ink: #1b1b22;
    --backdrop: #2c2c2f;
    --emblem-a: #1fb39a;
    --emblem-b: #2a9fd6;
  }
  * { margin: 0; padding: 0; box-sizing: border-box; }
  html, body { width: 1200px; height: 959px; overflow: hidden; }
  body {
    background: var(--backdrop);
    font-family: "Open Sans", Arial, sans-serif;
    position: relative;
  }
  .card {
    position: absolute;
    left: 220px;
    width: 760px;
    height: 434px;
    background: var(--white);
    overflow: hidden;
    box-shadow: 0 6px 18px rgba(0,0,0,0.35);
  }
  .card--back { top: 25px; }
  .card--front { top: 500px; }

  .band {
    position: absolute;
    left: 0;
    width: 100%;
    background: var(--navy);
  }
  .card--back .band { top: 190px; height: 175px; }
  .card--front .band { top: 250px; height: 150px; }

  .brand {
    position: absolute;
    display: flex;
    align-items: center;
    gap: 18px;
    color: var(--navy);
    font-weight: 700;
    white-space: nowrap;
  }
  .brand__mark {
    border-radius: 50%;
    background: var(--teal);
    flex: none;
  }
  .card--back .brand { left: 150px; top: 80px; font-size: 52px; z-index: 2; }
  .card--back .brand__mark { width: 110px; height: 110px; }

  .specialties {
    position: absolute;
    top: 220px;
    left: 120px;
    width: 440px;
    text-align: center;
    color: var(--white);
    z-index: 2;
  }
  .specialties__lead {
    font-family: "Courgette", cursive;
    font-size: 24px;
    margin-bottom: 8px;
  }
  .specialties__list { font-size: 17px; line-height: 1.45; }

  .social {
    position: absolute;
    right: 40px;
    top: 100px;
    display: flex;
    gap: 5px;
  }
  .social__dot {
    width: 18px; height: 18px;
    border-radius: 50%;
    background: var(--navy);
  }

  .emblem {
    position: absolute;
    left: 80px;
    top: 40px;
    width: 220px;
    height: 220px;
    border-radius: 50%;
    background: radial-gradient(circle at 40% 40%, var(--emblem-b), var(--emblem-a));
    z-index: 1;
  }
  .card--front .brand { left: 470px; top: 110px; font-size: 44px; }

  .person {
    position: absolute;
    left: 470px;
    top: 175px;
  }
  .person__name {
    color: var(--teal);
    font-weight: 700;
    font-size: 30px;
    letter-spacing: 1px;
    line-height: 1.1;
  }
  .person__title {
    color: var(--ink);
    font-weight: 600;
    font-size: 18px;
    letter-spacing: 1px;
    text-align: right;
    width: 225px;
  }

  .contact {
    position: absolute;
    left: 50px;
    top: 275px;
    color: var(--white);
    font-size: 17px;
    line-height: 1.6;
    z-index: 2;
  }
</style>
</head>
<body>

  <section class="card card--back" aria-label="Card back">
    <div class="band"></div>
    <div class="brand">
      <span class="brand__mark"></span>
      <span class="brand__name">Tumble Trips</span>
    </div>
    <div class="social" aria-label="Social links">
      <span class="social__dot"></span>
      <span class="social__dot"></span>
      <span class="social__dot"></span>
    </div>
    <div class="specialties">
      <p class="specialties__lead">Specializing in</p>
      <p class="specialties__list">Glimmerland destinations • Pelican Bay Fun Park<br>Cruises &amp; All-Inclusive Vacations.</p>
    </div>
  </section>

  <section class="card card--front" aria-label="Card front">
    <div class="band"></div>
    <div class="emblem" role="img" aria-label="Brand emblem area"></div>
    <div class="brand">
      <span class="brand__name">Tumble Trips</span>
    </div>
    <div class="person">
      <p class="person__name">MARLA QUINT</p>
      <p class="person__title">OWNER</p>
    </div>
    <div class="contact">
      <p>P: 555-647-1925 &nbsp;M: 555-218-4603 &nbsp;E: Marla@TumbleTrips.example</p>
      <p>W: www.TumbleTrips.example</p>
    </div>
  </section>

</body>
</html>
```